Kestrel Facilities Business Card Design

We would now like to design business cards with the new Kestrel Facilities logo

Target Market(s)

Professional

Industry/Entity Type

Professional services

Contact Information for Business Card

Employee name, title, phone number, email address, corporate office address and logo.

Font styles to use
Sans Serif

Colors
0054AA
0677BA
7BADD7
CADEEF
E8F1F8

Requirements
Must have
• My logo
Should not have
• any other pictures or images besides my logo

```html
<!DOCTYPE html>
<html lang="en">
<head>
<meta charset="utf-8">
<title>Kestrel Facilities – Business Card</title>
<link rel="stylesheet" href="https://fonts.googleapis.com/css2?family=Lato:wght@400;700;900&display=swap">
<style>
  :root {
    --brand-blue: #0780e6;
    --paper-white: #ffffff;
    --backdrop: #262626;
    --card-w: 760px;
    --card-h: 434px;
  }
  * { margin: 0; padding: 0; box-sizing: border-box; }
  html, body {
    width: 1200px;
    height: 1015px;
    overflow: hidden;
    background: var(--backdrop);
    font-family: "Lato", sans-serif;
  }
  .card {
    position: absolute;
    left: 220px;
    width: var(--card-w);
    height: var(--card-h);
    background: var(--brand-blue);
    overflow: hidden;
  }
  .card--front { top: 50px; }
  .card--back { top: 531px; }

  .brand {
    position: absolute;
    display: flex;
    align-items: center;
    gap: 18px;
    font-weight: 700;
    line-height: 1;
    letter-spacing: 0.5px;
    white-space: nowrap;
  }
  .brand__square { display: block; flex: none; }
  .card--front .brand {
    left: 50%;
    top: 50%;
    transform: translate(-50%, -50%);
    color: var(--paper-white);
    font-size: 46px;
  }
  .card--front .brand__square { width: 54px; height: 54px; background: var(--paper-white); }

  .back-art { position: absolute; inset: 0; }
  .card--back .brand {
    left: 430px;
    top: 132px;
    color: var(--brand-blue);
    font-size: 31px;
    gap: 16px;
  }
  .card--back .brand__square { width: 38px; height: 38px; background: var(--brand-blue); }

  .holder {
    position: absolute;
    left: 62px;
    top: 120px;
    color: var(--paper-white);
  }
  .holder__name { font-size: 27px; font-weight: 900; letter-spacing: 0.5px; }
  .holder__title { font-size: 20px; font-weight: 400; margin-top: 2px; }

  .contact {
    position: absolute;
    left: 62px;
    top: 262px;
    color: var(--paper-white);
    font-size: 19px;
    line-height: 1.25;
  }
  .contact__address { margin-bottom: 18px; }
  .contact__list { list-style: none; }
  .contact__list li { display: flex; align-items: center; gap: 10px; }
  .contact__icon { width: 18px; height: 18px; flex: none; }
</style>
</head>
<body>

  <section class="card card--front" aria-label="Card front">
    <div class="brand">
      <span class="brand__square"></span>
      <span class="brand__name">Kestrel Facilities</span>
    </div>
  </section>

  <section class="card card--back" aria-label="Card back">
    <svg class="back-art" viewBox="0 0 760 434" aria-hidden="true">
      <circle cx="640" cy="150" r="280" fill="#ffffff"/>
      <circle cx="626" cy="158" r="296" fill="none" stroke="#ffffff" stroke-width="3"/>
    </svg>

    <div class="brand">
      <span class="brand__square"></span>
      <span class="brand__name">Kestrel Facilities</span>
    </div>

    <div class="holder">
      <p class="holder__name">DANIEL HARPER</p>
      <p class="holder__title">Managing Director</p>
    </div>

    <div class="contact">
      <p class="contact__address">78, Harbour Row<br>Westfield, 30817</p>
      <ul class="contact__list">
        <li>
          <svg class="contact__icon" viewBox="0 0 24 24" aria-hidden="true"><path fill="#fff" d="M6.6 10.8a15.1 15.1 0 0 0 6.6 6.6l2.2-2.2a1 1 0 0 1 1-.25 11.4 11.4 0 0 0 3.6.57 1 1 0 0 1 1 1V20a1 1 0 0 1-1 1A17 17 0 0 1 3 4a1 1 0 0 1 1-1h3.5a1 1 0 0 1 1 1c0 1.25.2 2.450.57 3.57a1 1 0 0 1-.25 1z"/></svg>
          <span>044-555 019 274</span>
        </li>
        <li>
          <svg class="contact__icon" viewBox="0 0 24 24" aria-hidden="true"><path fill="#fff" d="M2 5h20v14H2z"/><path fill="none" stroke="#0780e6" stroke-width="1.6" d="M2.5 5.5 12 13l9.5-7.5"/></svg>
          <span>info@kestrelfm.com</span>
        </li>
        <li>
          <svg class="contact__icon" viewBox="0 0 24 24" aria-hidden="true"><g fill="none" stroke="#fff" stroke-width="1.8"><circle cx="12" cy="12" r="9.5"/><ellipse cx="12" cy="12" rx="4" ry="9.5"/><path d="M2.5 12h19M4 7h16M4 17h16"/></g></svg>
          <span>www.kestrelfm.com</span>
        </li>
      </ul>
    </div>
  </section>

</body>
</html>
```